Business Card Design

New business card design

Target Market(s)

Residential & Commercial Property Managers

Industry/Entity Type

Plumbing Services

Contact Information for Business Card

Name - Rowan Keddle, title - Director, Phone Number - 0431 286 517, email - rowan@tbk-plumbing.com.au, Company ABN - 73 215 904 386,

Font styles to use
Sans Serif

Colors
0054AA
0677BA
7BADD7
CADEEF
E8F1F8

```html
<!DOCTYPE html>
<html lang="en">
<head>
<meta charset="utf-8">
<title>TBK Plumbing Services – Business Card</title>
<link rel="stylesheet" href="https://fonts.googleapis.com/css2?family=Roboto:wght@300;400;500;700&display=swap">
<style>
  :root {
    --page-bg: #ededed;
    --card-white: #ffffff;
    --card-dark: #1f232b;
    --accent-blue: #0aa3e6;
    --ink-dark: #1c1f24;
    --ink-grey: #6b6f75;
    --ink-mid: #3d4046;
    --rim-blue: #0a9ee0;
  }
  * { box-sizing: border-box; margin: 0; padding: 0; }
  html, body {
    width: 1200px; height: 900px; overflow: hidden;
    background: var(--page-bg);
    font-family: "Roboto", Arial, sans-serif;
  }
  .stage {
    position: relative; width: 1200px; height: 900px;
    display: flex; align-items: center; justify-content: center; gap: 40px;
  }
  .card {
    position: relative; width: 540px; height: 309px;
    border-radius: 20px;
    border: 5px solid var(--rim-blue);
    overflow: hidden;
    box-shadow: 0 14px 30px rgba(0,0,0,0.18);
  }
  .card--front { background: var(--card-white); }
  .card--back  { background: var(--card-dark); }

  .name-band {
    position: absolute; left: 0; top: 24px;
    width: 330px; height: 38px;
    background: var(--accent-blue);
    display: flex; align-items: center; padding-left: 30px;
  }
  .name-band__name {
    color: #fff; font-weight: 700; font-size: 21px; letter-spacing: 0.2px;
    text-transform: uppercase;
  }
  .job-title {
    position: absolute; left: 30px; top: 68px;
    font-size: 13px; color: var(--ink-grey); font-weight: 400;
  }
  .brand {
    position: absolute; display: flex; align-items: center; gap: 8px;
  }
  .brand__dot {
    width: 12px; height: 12px; border-radius: 50%; background: var(--accent-blue);
    flex: none;
  }
  .brand__name {
    font-weight: 300; font-size: 22px; white-space: nowrap;
  }
  .card--front .brand { right: 22px; top: 80px; }
  .card--front .brand__name { color: var(--ink-dark); }
  .card--back .brand { left: 80px; top: 96px; }
  .card--back .brand__name { color: #ffffff; font-size: 30px; }

  .contact-list {
    position: absolute; left: 26px; top: 150px;
    list-style: none; display: flex; flex-direction: column; gap: 6px;
  }
  .contact-list__item {
    display: flex; align-items: center; gap: 7px;
    font-size: 15px; color: var(--ink-mid);
  }
  .contact-list__icon { width: 13px; height: 13px; flex: none; }
  .abn {
    position: absolute; right: 24px; bottom: 22px;
    font-size: 19px; color: var(--ink-mid);
  }
  .abn__label { color: var(--accent-blue); }
</style>
</head>
<body>
  <main class="stage">
    <section class="card card--front" aria-label="Business card front">
      <div class="name-band"><span class="name-band__name">Rowan Keddle</span></div>
      <p class="job-title">Director</p>

      <div class="brand">
        <span class="brand__dot"></span>
        <span class="brand__name">TBK Plumbing Services</span>
      </div>

      <ul class="contact-list">
        <li class="contact-list__item">
          <svg class="contact-list__icon" viewBox="0 0 16 16" aria-hidden="true">
            <rect x="0" y="0" width="16" height="16" rx="3" fill="var(--accent-blue)"/>
            <path d="M5 3.5c.6 0 1 .9 1.3 1.7.2.5-.6 1-.5 1.4.3.9 1.4 2.1 2.4 2.5.4.1.9-.7 1.4-.5.8.3 1.7.7 1.7 1.3 0 1-1 1.9-2 1.8C6.6 11.4 4.3 9 4 6 3.9 4.6 4.3 3.5 5 3.5z" fill="#fff"/>
          </svg>
          0431 286 517
        </li>
        <li class="contact-list__item">
          <svg class="contact-list__icon" viewBox="0 0 16 16" aria-hidden="true">
            <rect x="0" y="0" width="16" height="16" rx="3" fill="var(--accent-blue)"/>
            <rect x="3" y="4.5" width="10" height="7" rx="1" fill="#fff"/>
            <path d="M3.3 5l4.7 3.6L12.7 5" stroke="var(--accent-blue)" stroke-width="1" fill="none"/>
          </svg>
          rowan@tbk-plumbing.com.au
        </li>
      </ul>

      <p class="abn"><span class="abn__label">ABN:</span> 73 215 904 386</p>
    </section>

    <section class="card card--back" aria-label="Business card back">
      <div class="brand">
        <span class="brand__dot"></span>
        <span class="brand__name">TBK Plumbing Services</span>
      </div>
    </section>
  </main>
</body>
</html>
```